Brintel Works - Fast, Efficient and Gas Mainteance for Domestic, Commercial and Industrial clients

We are in the process of purchasing a new business and would like to get a new logo and business card.
Business is a gas maintenance business that also does new gas installations.
Has been established since 1988.
Services include:
Install all types of gas appliances & equipment inc. hot water units
Maintain / repair / replace all types of gas appliances & equipment

Target Market(s)

Domestic, Commercial and Industrial clients

Industry/Entity Type

Business

Contact Information for Business Card

admin@brintelworks.com.au
07 3918 4726
Brintel Works PTY LTD

Logo Text

Gas Fitting & Plumbing Maintenance Specialists

Font styles to use
Sans Serif

Requirements
Must have
• Logo
• Business name, contact number, email address, web address
• Domestic | Commercial | Industrial Est Since 1988
Nice to have
• Possibly a black card with a flame logo to one side
Should not have
• Spelling errors

```html
<!DOCTYPE html>
<html lang="en">
<head>
<meta charset="utf-8">
<title>Brintel Works – Business Card</title>
<link href="https://fonts.googleapis.com/css2?family=Source+Sans+3:wght@400;600;700&display=swap" rel="stylesheet">
<style>
  :root {
    --backdrop: #a9a9a7;
    --card-black: #050505;
    --flame-red: #e82427;
    --flame-yellow: #f7d11e;
    --flame-orange: #f47b20;
    --text-white: #ffffff;
    --tagline-gold: #e9c21a;
  }
  * { box-sizing: border-box; margin: 0; padding: 0; }
  html, body { width: 1200px; height: 900px; overflow: hidden; }
  body {
    background: var(--backdrop);
    font-family: "Source Sans 3", Arial, sans-serif;
    position: relative;
  }
  .card {
    position: absolute;
    width: 540px;
    height: 310px;
    background: var(--card-black);
    box-shadow: 0 6px 18px rgba(0,0,0,.3);
    overflow: hidden;
  }
  /* Front */
  .card--front { left: 600px; top: 110px; }
  .front-brand {
    position: absolute; left: 0; right: 0; top: 100px;
    text-align: center; color: var(--flame-yellow);
  }
  .front-brand__name { font-size: 44px; font-weight: 700; line-height: 1; }
  .front-brand__suffix { font-size: 14px; font-weight: 700; letter-spacing: 4px; margin-top: 4px; }
  .front-tagline {
    position: absolute; left: 0; right: 0; top: 212px;
    text-align: center; color: var(--tagline-gold); font-size: 16px;
  }
  /* Back */
  .card--back { left: 70px; top: 470px; }
  .back-art { position: absolute; inset: 0; }
  .back-brand {
    position: absolute; left: 30px; top: 138px;
    color: var(--flame-yellow); font-size: 30px; font-weight: 700;
  }
  .contact {
    position: absolute; right: 26px; top: 92px;
    color: var(--text-white); text-align: right; font-size: 17px; line-height: 1.2;
  }
  .contact__address { margin-bottom: 22px; }
  .contact__line { display: flex; justify-content: flex-end; align-items: center; gap: 8px; }
  .contact__icon { width: 13px; height: 13px; flex: none; }
</style>
</head>
<body>
  <section class="card card--front" aria-label="Business card front">
    <div class="front-brand">
      <div class="front-brand__name">Brintel Works</div>
      <div class="front-brand__suffix">PTY LTD</div>
    </div>
    <p class="front-tagline">Domestic | Commercial | Industrial Est Since 1988</p>
  </section>

  <section class="card card--back" aria-label="Business card back">
    <svg class="back-art" viewBox="0 0 540 310" width="540" height="310" aria-hidden="true">
      <path d="M250,0 C350,70 345,230 180,310 L540,310 L540,0 Z" fill="var(--flame-red)"/>
      <path d="M238,0 L262,0 C330,40 345,120 322,170 C338,110 310,40 238,0 Z" fill="var(--flame-yellow)"/>
      <path d="M330,150 C315,230 260,285 165,310 L195,310 C280,280 330,230 330,150 Z" fill="var(--flame-orange)"/>
    </svg>
    <div class="back-brand">Brintel Works</div>
    <div class="contact">
      <p class="contact__address">12345, Address Goes Here<br>Country Name, 123456.</p>
      <p class="contact__line">07 3918 4726
        <svg class="contact__icon" viewBox="0 0 16 16"><path fill="#fff" d="M3 1l3 3-2 2c1 2 3 4 5 5l2-2 3 3-2 3C7 15 1 9 1 3z"/></svg></p>
      <p class="contact__line">admin@brintelworks.com.au
        <svg class="contact__icon" viewBox="0 0 16 16"><rect x="1" y="3" width="14" height="10" fill="none" stroke="#fff" stroke-width="1.5"/><path d="M1 3l7 6 7-6" fill="none" stroke="#fff" stroke-width="1.5"/></svg></p>
      <p class="contact__line">www.brintelworks.com.au
        <svg class="contact__icon" viewBox="0 0 16 16"><circle cx="8" cy="8" r="6.5" fill="none" stroke="#fff" stroke-width="1.4"/><path d="M1.5 8h13M8 1.5c-3 3.5-3 9.5 0 13M8 1.5c3 3.5 3 9.5 0 13" fill="none" stroke="#fff" stroke-width="1.2"/></svg></p>
    </div>
  </section>
</body>
</html>
```